Homepage for the brisk-find Web Application

At the end of this text, you will find a link to a website that is under construction for a webApp that I intend to launch soon. The contest goal is for you to make redesign the homepage in a nice, fresh, modern Style. Only design, no coding necessary. It needs to have a responsive version for small screens like smart phones. Attached is the text for it, and some images that you may use. You are welcome to find or create additional supporting images. You can use PixTrove.example or similar service to find new images as long as I can purchase the non-exclusive use rights for the images at similar prices. The contest is just for the home page. However, the winner, if I like the work and we can agree on a fair price, could be contracted on a one-on-one basis to do the rest of the site. You are welcome to suggest minor changes like font sizes and minor variations on the Header banner, but that banner is consistent with the user interface of the application therefore should not change too much. The information should flow somewhat continually without much use of side bars or things like that.
https://www.brisk-find.example
Sincerely,
Marco D. Ferral

```html
<!DOCTYPE html>
<html lang="en">
<head>
<meta charset="utf-8">
<title>Brisk-Find — Find any document or item instantly</title>
<link rel="stylesheet" href="https://fonts.googleapis.com/css2?family=Arimo:wght@400;700&family=Archivo+Black&display=swap">
<style>
:root{
  --teal:#3bb5bf;
  --orange:#ef6239;
  --navy:#1b3a6b;
  --ink:#333;
  --sky:#d6f0f8;
  --blush:#f1d9d2;
  --grey:#f0f0f0;
  --white:#fff;
  --deep-red:#b5361b;
}
*{margin:0;padding:0;box-sizing:border-box}
html,body{width:1200px;height:3471px;overflow:hidden}
body{position:relative;font-family:"Arimo",Arial,sans-serif;color:var(--ink);background:var(--white)}
.abs{position:absolute}
.band{position:absolute;left:0;width:1200px}
.hero{top:0;height:486px;background:linear-gradient(100deg,#52c6bd 0%,#2e8fd0 45%,#0d45dc 75%,#0a3ad8 100%)}
.brand{position:absolute;left:150px;top:20px;display:flex;align-items:center;gap:8px;font-size:24px;color:var(--white)}
.brand-dot{width:30px;height:30px;border-radius:50%;border:3px solid var(--navy);background:var(--white)}
.nav{position:absolute;top:30px;font-size:11px;color:var(--white)}
.signup{position:absolute;left:974px;top:26px;width:75px;height:22px;border-radius:11px;background:var(--orange);color:var(--white);font-size:11px;text-align:center;line-height:22px}
.hero-title{position:absolute;left:150px;top:140px;font-family:"Archivo Black",sans-serif;font-size:26px;color:var(--navy);letter-spacing:.2px}
.hero-copy{position:absolute;left:150px;top:203px;width:530px;font-size:13.5px;line-height:20.3px;color:var(--white)}
.hero-strong{position:absolute;left:150px;top:345px;width:530px;font-size:13.5px;line-height:20.3px;font-weight:700;color:var(--white)}
.cta{position:absolute;left:150px;top:407px;width:185px;height:28px;border-radius:14px;background:var(--orange);color:var(--white);font-size:10.5px;text-align:center;line-height:28px}
.art{position:absolute;border-radius:26px;background:linear-gradient(160deg,#b9f0f5 0%,#47c3cf 60%,#1f9fb1 100%)}
.art.warm{background:linear-gradient(160deg,#bff2f6 0%,#4fc7d2 55%,#f07a55 100%)}
.why{top:486px;height:384px;background:var(--white)}
.title{position:absolute;font-size:18px;font-weight:700;color:var(--teal);text-align:center;white-space:nowrap}
.title span{color:var(--orange)}
.point{position:absolute;font-size:11.5px;line-height:16px;color:var(--ink)}
.storage{top:870px;height:1447px;background:var(--grey)}
.sub{position:absolute;font-size:15px;color:var(--teal)}
.body{position:absolute;font-size:12.2px;line-height:18px;color:var(--ink)}
.item-title{position:absolute;font-size:12px;line-height:15px;color:var(--orange)}
.item-body{position:absolute;font-size:8.6px;line-height:15.8px;color:#444}
.left{text-align:right}
.alt{top:2317px;height:447px;background:var(--white)}
.reviews{top:2764px;height:391px;background:var(--grey)}
.card{position:absolute;top:2889px;width:425px;height:182px;border:1px solid var(--orange);border-radius:28px;background:var(--white)}
.card .quote{position:absolute;left:24px;top:-14px;font-family:Georgia,serif;font-size:150px;line-height:150px;color:#f6cfc3}
.card h3{position:absolute;left:0;right:0;top:50px;text-align:center;font-weight:400;font-size:15px;color:var(--orange)}
.card p{position:absolute;left:20px;right:20px;top:88px;text-align:center;font-size:8.6px;line-height:15px;color:#444}
.avatar{position:absolute;top:2855px;width:68px;height:68px;border-radius:50%;border:2px solid var(--orange);background:radial-gradient(circle at 50% 40%,#e6d8d0,#9c8c85)}
.dot{position:absolute;top:3103px;width:13px;height:13px;border-radius:50%;background:#3fc3ee}
.footer{top:3155px;height:301px;background:var(--orange);color:var(--white)}
.foot-h{position:absolute;font-size:19px;font-weight:700;color:var(--white)}
.foot-t{position:absolute;font-size:10.3px;line-height:15.6px;color:var(--white)}
.foot-link{position:absolute;font-size:10.5px;font-weight:700;color:var(--white)}
.social{position:absolute;width:26px;height:26px;border-radius:50%;border:2.5px solid var(--white)}
.legal{top:3456px;height:15px;background:var(--deep-red);color:var(--white);font-size:8px;text-align:center;line-height:15px}
.lines{position:absolute;left:0;top:0;width:1200px;height:3471px;pointer-events:none}
</style>
</head>
<body>

<!-- Header / hero -->
<section class="band hero">
  <div class="brand"><span class="brand-dot"></span><span>Brisk-Find</span></div>
  <span class="nav" style="left:412px">About</span>
  <span class="nav" style="left:478px">Pricing</span>
  <span class="nav" style="left:548px">Blog</span>
  <span class="nav" style="left:607px">FAQs</span>
  <span class="nav" style="left:671px">Suppor</span>
  <span class="nav" style="left:743px">Reviews</span>
  <span class="nav" style="left:821px">Contact Us</span>
  <span class="nav" style="left:910px">Free-Trail</span>
  <span class="signup">Sign up</span>

  <h1 class="hero-title">Find any document or item instantly!</h1>
  <p class="hero-copy">Brisk-Find is a system that allows you to quickly search for the location of every item that you store or file. It is an essential tool for keeping track of paper documents or any other kind of physical item. You’ll have the ability to quickly find any item you’re searching for, even years after you’ve stored it. More importantly, using Brisk-Find helps you save considerable space without losing speedy accessibility to your treasured items.</p>
  <p class="hero-strong">Keeping track of all your paper documents and other belongings has never been easier!</p>
  <span class="cta">START 30 DAY FREE TRIAL</span>
  <div class="art warm" role="img" aria-label="Illustration of a smartphone opening like a filing drawer, with a person pulling out a large folder" style="left:756px;top:104px;width:290px;height:340px"></div>
</section>

<!-- Why section -->
<section class="band why">
  <div class="abs" style="left:885px;top:0;width:315px;height:268px;background:var(--sky)"></div>
  <h2 class="title" style="left:0;width:1186px;top:40px">Why <span>Brisk-Find?</span></h2>
  <p class="point" style="left:682px;top:111px">It is extremely easy to use.</p>
  <p class="point" style="left:275px;top:162px;width:240px">It Adapts to your stile. Since each catalog can have 1 or more levels of depth (folders and sub-folders), Brisk-Find does not force you to use a specific filing or storage methodology.</p>
  <p class="point" style="left:682px;top:213px;width:230px">It’s very affordable. Checkout our pricing plans!</p>
  <p class="point" style="left:276px;top:264px;width:230px">Since it is online, your data is available almost anywhere in the world.</p>
  <p class="point" style="left:682px;top:316px;width:290px">Data encryption ensures that your information is always private, safe, and secure.</p>
</section>

<!-- Storage management section -->
<section class="band storage">
  <div class="abs" style="left:0;top:0;width:313px;height:268px;background:var(--blush)"></div>
  <div class="abs" style="left:889px;top:322px;width:311px;height:267px;background:var(--sky)"></div>
  <div class="abs" style="left:0;top:1180px;width:313px;height:267px;background:var(--sky)"></div>
  <h2 class="title" style="left:0;width:1200px;top:27px">Why use a storage management system like <span>Brisk-Find?</span></h2>
  <div class="art warm" role="img" aria-label="Illustration of a smartphone drawer with a person holding a large disc case" style="left:232px;top:85px;width:270px;height:340px"></div>

  <h3 class="sub" style="left:539px;top:107px">Managing paper documents</h3>
  <p class="body" style="left:540px;top:146px;width:475px">Most people and businesses have a variety of documents that need to be filed. The problem is how to do it efficiently so that anything you need can easily be found, even well into the future. Normally, you’d put them in folders on file drawers, sorted in some sort of fashion. But which standard is correct for all kinds of documents? There is no set criterion for every kind of document, so you need to use a combination of them.</p>
  <p class="body" style="left:540px;top:253px;width:475px">As time passes, you might have a difficult time recalling what criterion you used to file your documents, making it hard to find that document with ease. You might not even find it at all. It becomes even more complex when the person doing the searching isn’t the same one as who filed it years ago.</p>
  <p class="body" style="left:540px;top:344px;width:475px">It is estimated that workers spend over 20% of their time managing documents. A storage management system like Brisk-Find allows any authorized user to instantly find any document regardless of who filed it or which criterion was used, as long as it was properly filed using the system.</p>

  <h3 class="sub" style="left:0;width:1200px;text-align:center;top:574px">Managing any non-document objects</h3>
  <p class="body" style="left:0;width:1200px;text-align:center;top:609px">The same is true of storing any other kind of objects. Common examples include:</p>

  <div class="art" role="img" aria-label="Illustration of a large smartphone showing open folders holding a document, wine bottle, disc, key and test tubes" style="left:458px;top:700px;width:283px;height:680px;border-radius:40px"></div>

  <p class="item-title left" style="left:160px;width:203px;top:824px">Storage boxes, closets, warehouses,and shelves</p>
  <p class="item-body left" style="left:160px;width:205px;top:865px">In storage, would better be indexed with a system that lets you find what you’re looking for instantly. Otherwise, you are better off getting rid of those items. In addition to helping you find any object quickly and easily, proper use of Brisk-Find could help you save lots of space!</p>
  <p class="item-title left" style="left:160px;width:201px;top:985px">Books</p>
  <p class="item-body left" style="left:160px;width:203px;top:1007px">Whether you keep your books on display on shelves, or stored in boxes, you should keep them indexed if you ever want to find any of them in the future.</p>
  <p class="item-title left" style="left:160px;width:199px;top:1079px">Wines</p>
  <p class="item-body left" style="left:160px;width:201px;top:1101px">Maintaining a constant temperature is essential for good care of quality wines. If you are a wine enthusiast, and have even a small wine cellar fridge, keepin your wines indexed on our system would prove invaluable in selecting and locating a wine bottle for any moment without opening that cellar fridge door for too long.</p>
  <p class="item-title left" style="left:160px;width:200px;top:1236px">Safety boxes</p>
  <p class="item-body left" style="left:160px;width:202px;top:1260px">It is common for people to forget exactly which valuables they have stored in their safety boxes or bank safety deposit boxes.</p>

  <p class="item-title" style="left:834px;top:763px">Moving boxes</p>
  <p class="item-body" style="left:836px;width:222px;top:787px">It is always a good idea to record in detail the contents of each box when you move. Since Brisk-Find works well on any modern smartphone, it is easy to record each item as you pack it. After the move, the system makes it easy for you to check that everything that you packed arrived as it should. In addition, if you leave some boxes unopened for a long time, you will always be able to locate the items inside in no time.</p>
  <p class="item-title" style="left:836px;top:936px">Test samples</p>
  <p class="item-body" style="left:838px;width:222px;top:960px">Laboratory samples frequently need to be stored at constant cold temperatures. Our system was originally designed to fulfill the needs of a laboratory which needs an efficient way to minimize the time that the door of their specialized freezers is open while searching for a sample. For confidentiality reasons, each vial was only identified with a code and all the details of the sample and patient would be recorded on our secure system.</p>
  <p class="item-title" style="left:836px;top:1111px;width:200px">Audio, video, data, and removable media</p>
  <p class="item-body" style="left:838px;width:222px;top:1150px">Keeping track of the content and storage location of removable media can be a hassle. A system like ours can really help to make that task a breeze.</p>
  <p class="item-title" style="left:837px;top:1222px">Keys</p>
  <p class="item-body" style="left:838px;width:222px;top:1246px">In a situation such a property management, you can keep track of hundreds of keys for every property you manage. Using Brisk-Find will easily organize your key boxes without losing track of where the keys for each property are located.</p>
</section>

<!-- Alternative uses -->
<section class="band alt">
  <div class="abs" style="left:882px;top:0;width:318px;height:263px;background:var(--sky)"></div>
  <h2 class="title" style="left:0;width:1086px;top:153px">Alternative uses for <span>Brisk-Find</span></h2>
  <p class="body" style="left:286px;top:204px;width:400px;text-align:center">How many times have you gone to a restaurant and couldn’t recall how good (or bad) each of the dishes were that you previously ordered? You can use Brisk-Find to record each one to improve your experience for every visit. Our app can also help you decide where you want to go or which dish to recommend when you have a special occasion.</p>
  <div class="art warm" role="img" aria-label="Illustration of a smartphone drawer with a person holding a large wine bottle" style="left:724px;top:94px;width:172px;height:270px"></div>
</section>

<!-- Testimonials -->
<section class="band reviews">
  <div class="abs" style="left:0;top:0;width:310px;height:267px;background:var(--sky)"></div>
  <h2 class="title" style="left:0;width:1200px;top:36px">Clients <span>Testomonials</span></h2>
</section>
<article class="card" style="left:150px">
  <span class="quote">“</span>
  <h3>Nora P. Vale</h3>
  <p>Nulla elementum efficitur ullamcorper. Morbi finibus euismod mollis. Cras scelerisque luctus elit, nec convallis augue vestibulum ut. Nulla dapibus diam vitae posuere bibendum. Ut quis erat vitae nibh feugiat dignissim. Nulla facilisi. Sed dictum, massa in vehicula finibus, dui ante elementum ex, non aliquet purus libero eget urna.</p>
</article>
<article class="card" style="left:626px">
  <span class="quote">“</span>
  <h3>Clara M. Lund</h3>
  <p>Donec vitae lobortis risus. Vestibulum fringilla nibh risus, et mollis turpis lacinia a. Integer eu scelerisque neque. Fusce metus quam, sagittis in tincidunt ultricies, efficitur vulputate mi. Vestibulum accumsan lacus eros, quis tincidunt est varius vitae. Ut id ligula id quam tempor auctor in id purus. Nullam ultricies condimentum libero sit amet faucibus.</p>
</article>
<div class="avatar" role="img" aria-label="Portrait photo of the client" style="left:328px"></div>
<div class="avatar" role="img" aria-label="Portrait photo of the client" style="left:804px"></div>
<span class="dot" style="left:550px"></span>
<span class="dot" style="left:572px"></span>
<span class="dot" style="left:593px;top:3101px;width:16px;height:16px;background:var(--orange)"></span>
<span class="dot" style="left:616px"></span>
<span class="dot" style="left:638px"></span>

<!-- Footer -->
<footer class="band footer">
  <h4 class="foot-h" style="left:151px;top:30px">About Us</h4>
  <p class="foot-t" style="left:151px;top:69px;width:210px">Quisque condimentum augue nec odio volutpat, sit amet auctor est volutpat. Suspendisse potenti. Aenean non gravida sapien. Donec gravida aliquam dolor, eu viverra nisi pretium vel. Maecenas id ornare leo. Sed lacinia tristique est, in viverra massa suscipit ac. Duis ac massa tincidunt, pharetra urna vel, pulvinar lorem. Maecenas hendrerit dui et massa euismod mollis. Aliquam risus urna, pharetra eu vulputate sit amet.</p>
  <h4 class="foot-h" style="left:431px;top:30px">Quick Links</h4>
  <span class="foot-link" style="left:434px;top:80px">About</span>
  <span class="foot-link" style="left:434px;top:105px">Pricing</span>
  <span class="foot-link" style="left:434px;top:131px">Blog</span>
  <span class="foot-link" style="left:434px;top:156px">FAQs</span>
  <span class="foot-link" style="left:504px;top:78px">Suppor</span>
  <span class="foot-link" style="left:504px;top:103px">Reviews</span>
  <span class="foot-link" style="left:504px;top:129px">Contact Us</span>
  <span class="foot-link" style="left:504px;top:154px">Free-Trail</span>
  <h4 class="foot-h" style="left:645px;top:30px">Contact</h4>
  <svg class="abs" style="left:646px;top:97px" width="20" height="20" viewBox="0 0 24 24" aria-hidden="true"><path fill="#fff" d="M6.6 10.8a15 15 0 0 0 6.6 6.6l2.2-2.2c.3-.3.7-.4 1-.2 1.1.4 2.3.6 3.6.6.6 0 1 .4 1 1V20c0 .6-.4 1-1 1A17 17 0 0 1 3 4c0-.6.4-1 1-1h3.5c.6 0 1 .4 1 1 0 1.3.2 2.5.6 3.6.1.3 0 .7-.2 1z"/></svg>
  <span class="foot-t" style="left:675px;top:98px">(555)-014-2287</span>
  <svg class="abs" style="left:646px;top:135px" width="21" height="15" viewBox="0 0 21 15" aria-hidden="true"><rect x="0.5" y="0.5" width="20" height="14" fill="none" stroke="#fff"/><path d="M1 1l9.5 7L20 1" fill="none" stroke="#fff" stroke-width="1.5"/></svg>
  <span class="foot-t" style="left:675px;top:134px">hello@brisk-find.example</span>
  <h4 class="foot-h" style="left:839px;top:30px">Location</h4>
  <p class="foot-t" style="left:841px;top:76px;width:215px">sit amet, finibus in risus. Nunc viverra sapien a maximus dictum. Mauris bibendum at magna rutrum Maecenas hendrerit dui et massa euismod mollis. Aliquam risus urna, pharetra eu vulputate</p>
  <h4 class="foot-h" style="left:841px;top:183px">Keep Connected</h4>
  <span class="social" style="left:841px;top:216px"></span>
  <span class="social" style="left:889px;top:216px"></span>
  <span class="social" style="left:841px;top:256px"></span>
  <span class="social" style="left:889px;top:256px"></span>
</footer>
<div class="band legal">© All Rights are reserved</div>

<!-- Connector lines -->
<svg class="lines" viewBox="0 0 1200 3471" aria-hidden="true">
  <g stroke="#3bb5bf" stroke-width="1.5" fill="none">
    <line x1="593" y1="555" x2="593" y2="870"/>
    <line x1="593" y1="605" x2="670" y2="605"/>
    <line x1="593" y1="656" x2="515" y2="656"/>
    <line x1="593" y1="707" x2="670" y2="707"/>
    <line x1="593" y1="758" x2="515" y2="758"/>
    <line x1="593" y1="810" x2="670" y2="810"/>

    <line x1="436" y1="1728" x2="436" y2="2173"/>
    <line x1="374" y1="1705" x2="436" y2="1752"/>
    <line x1="374" y1="1863" x2="436" y2="1923"/>
    <line x1="374" y1="1957" x2="436" y2="2018"/>
    <line x1="374" y1="2115" x2="436" y2="2173"/>

    <line x1="761" y1="1569" x2="761" y2="2034"/>
    <line x1="761" y1="1569" x2="824" y2="1632"/>
    <line x1="761" y1="1748" x2="824" y2="1805"/>
    <line x1="761" y1="1923" x2="824" y2="1983"/>
    <line x1="761" y1="2034" x2="824" y2="2095"/>
  </g>
  <g fill="#ef6239">
    <circle cx="593" cy="605" r="7.5"/><circle cx="593" cy="656" r="7.5"/><circle cx="593" cy="707" r="7.5"/><circle cx="593" cy="758" r="7.5"/><circle cx="593" cy="810" r="7.5"/>
    <circle cx="670" cy="605" r="2.5"/><circle cx="515" cy="656" r="2.5"/><circle cx="670" cy="707" r="2.5"/><circle cx="515" cy="758" r="2.5"/><circle cx="670" cy="810" r="2.5"/>
    <circle cx="374" cy="1705" r="2.5"/><circle cx="374" cy="1863" r="2.5"/><circle cx="374" cy="1957" r="2.5"/><circle cx="374" cy="2115" r="2.5"/>
    <circle cx="436" cy="1752" r="2.5"/><circle cx="436" cy="1923" r="2.5"/><circle cx="436" cy="2018" r="2.5"/><circle cx="436" cy="2173" r="2.5"/>
    <circle cx="761" cy="1569" r="2.5"/><circle cx="761" cy="1748" r="2.5"/><circle cx="761" cy="1923" r="2.5"/><circle cx="761" cy="2034" r="2.5"/>
    <circle cx="824" cy="1632" r="2.5"/><circle cx="824" cy="1805" r="2.5"/><circle cx="824" cy="1983" r="2.5"/><circle cx="824" cy="2095" r="2.5"/>
  </g>
</svg>

</body>
</html>
```